Business cards to launch an education platform

Hi,
I am looking at having new business cards designed.
I am a startup, developing a web platform for schools and university, the education world. It's an online assessment system.
I would like a card that looks classy, and that is using the colors and the font of my logo.

I have attached:
1) my logo
2) A business card that I have designed quickly so you can have all the information required in the card, but I really don't like it.
3) The font that I am using (Lato Regular) to design my web platform
4) Some screenshots of my web platform so you can have a look at the style that I have.

Target Market(s)

Major market: Education system: Schools and university
Minor markets: Business in general

Industry/Entity Type

Business

Contact Information for Business Card

Clara Fenwick
Director

M: 0437 518 902
E: clara.fenwick@amberLoomSystems.com.au

Requirements
Must have
• The colors of my logo

```html
<!DOCTYPE html>
<html lang="en">
<head>
<meta charset="UTF-8">
<title>Amber Loom Systems – Business Cards</title>
<link rel="stylesheet" href="https://fonts.googleapis.com/css2?family=Open+Sans:wght@300;400;600&display=swap">
<style>
  :root {
    --page-bg: #e9ebee;
    --card-white: #ffffff;
    --brand-blue: #1f5fa8;
    --brand-blue-deep: #0f3f80;
    --brand-blue-light: #2f86cf;
    --accent-cyan: #3cc3ef;
    --text-on-blue: #ffffff;
    --text-soft: #d6e6f6;
  }
  * { box-sizing: border-box; margin: 0; padding: 0; }
  html, body {
    width: 1200px;
    height: 950px;
    overflow: hidden;
    background: var(--page-bg);
    font-family: "Open Sans", sans-serif;
  }
  .canvas {
    width: 1200px;
    height: 950px;
    display: flex;
    flex-direction: column;
    align-items: center;
    justify-content: center;
    gap: 34px;
  }
  .card {
    position: relative;
    width: 760px;
    height: 434px;
    overflow: hidden;
    border-radius: 4px;
    box-shadow: 0 10px 28px rgba(15, 40, 80, 0.22);
  }

  /* Front */
  .card-front { background: var(--card-white); }
  .card-front .panel-shape {
    position: absolute;
    inset: 0;
    width: 100%;
    height: 100%;
  }
  .brand-block {
    position: absolute;
    left: 48px;
    top: 178px;
    width: 350px;
    display: flex;
    align-items: center;
    gap: 16px;
  }
  .brand-square {
    flex: 0 0 68px;
    width: 68px;
    height: 68px;
    background: var(--brand-blue);
  }
  .brand-name {
    color: var(--brand-blue);
    font-weight: 300;
    line-height: 1;
    white-space: nowrap;
  }
  .brand-name .line-main {
    display: block;
    font-size: 32px;
    letter-spacing: 2px;
  }
  .brand-name .line-sub {
    display: block;
    font-size: 22px;
    letter-spacing: 3px;
    margin-top: 6px;
  }
  .contact-block {
    position: absolute;
    left: 478px;
    right: 28px;
    top: 178px;
    color: var(--text-on-blue);
    white-space: nowrap;
  }
  .contact-name {
    font-size: 18px;
    font-weight: 600;
    letter-spacing: 0.4px;
  }
  .contact-name .role {
    font-weight: 300;
    font-size: 14px;
  }
  .contact-phone {
    margin-top: 12px;
    font-size: 14px;
    font-weight: 300;
    color: var(--text-soft);
  }
  .contact-email {
    margin-top: 18px;
    font-size: 12.5px;
    font-weight: 300;
    color: var(--text-soft);
  }

  /* Back */
  .card-back {
    background:
      linear-gradient(125deg, rgba(255,255,255,0.10) 0%, rgba(255,255,255,0) 45%),
      linear-gradient(160deg, var(--brand-blue-light) 0%, var(--brand-blue) 45%, var(--brand-blue-deep) 100%);
  }
  .back-brand {
    position: absolute;
    left: 0;
    right: 0;
    top: 138px;
    text-align: center;
    color: var(--text-on-blue);
    font-weight: 300;
    line-height: 1;
  }
  .back-brand .line-main {
    display: block;
    font-size: 58px;
    letter-spacing: 6px;
  }
  .back-brand .line-sub {
    display: block;
    font-size: 38px;
    letter-spacing: 5px;
    margin-top: 10px;
  }
  .back-web {
    position: absolute;
    left: 0;
    right: 0;
    top: 282px;
    text-align: center;
    color: var(--text-soft);
    font-size: 17px;
    font-weight: 300;
    letter-spacing: 1px;
  }
</style>
</head>
<body>
<main class="canvas">
  <section class="card card-front" aria-label="Business card front">
    <svg class="panel-shape" viewBox="0 0 760 434" aria-hidden="true">
      <defs>
        <linearGradient id="panelBlue" x1="0" y1="0" x2="1" y2="1">
          <stop offset="0" stop-color="#2a73bd"/>
          <stop offset="1" stop-color="#123f7d"/>
        </linearGradient>
      </defs>
      <polyline points="428,0 428,44 448,62 428,80 428,434"
                fill="none" stroke="var(--accent-cyan)" stroke-width="3"/>
      <polygon points="440,0 760,0 760,434 440,434 440,80 460,62 440,44"
               fill="url(#panelBlue)"/>
    </svg>
    <div class="brand-block">
      <div class="brand-square"></div>
      <div class="brand-name">
        <span class="line-main">AMBER LOOM</span>
        <span class="line-sub">Systems</span>
      </div>
    </div>
    <div class="contact-block">
      <p class="contact-name">CLARA FENWICK <span class="role">- DIRECTOR</span></p>
      <p class="contact-phone">0437 518 902</p>
      <p class="contact-email">clara.fenwick@amberLoomSystems.com.au</p>
    </div>
  </section>

  <section class="card card-back" aria-label="Business card back">
    <div class="back-brand">
      <span class="line-main">AMBER LOOM</span>
      <span class="line-sub">Systems</span>
    </div>
    <p class="back-web">amberLoomSystems.com.au</p>
  </section>
</main>
</body>
</html>
```